Website for software company "velora"

We need a website for our software company/startup named "velora". We are developing several products (currently 3 standard-software products) which are all in different sectors, but all our products are available for Laptops/PC/Mobile Phones/Tablets, ... We do also create custom software and support our customers with consulting to optimize their processes.
We already have a Logo which you can find in the attached files.
We are a young team of 4 members (two founders and 2 employees).

To get an idea of our products -> the first one is a planning software for healthcare organizations (eg. BlueHaven, firebrigade, pharmacy), the second one is a booking software for sport clubs and the third one is a competition software for sports hunting. You see very diverse. Include or ignore this info of our products as you like.

The design has to be a bootstrap 4 (or higher) design. We have licenced FontAwesome as iconset. Responsive design should come without saying.

• Starting page, product pages, news section, contact, team, services

```html
<!DOCTYPE html>
<html lang="en">
<head>
<meta charset="utf-8">
<title>velora — Home Page Concepts</title>
<link href="https://fonts.googleapis.com/css2?family=Poppins:wght@400;500;600;700&display=swap" rel="stylesheet">
<style>
:root{
  --orange:#f26b1d;
  --orange-soft:#f89a5c;
  --dark:#1e232d;
  --dark-2:#2b313d;
  --ink:#23262d;
  --grey:#7a7f88;
  --light:#f2f2f3;
  --white:#ffffff;
}
*{box-sizing:border-box;margin:0;padding:0}
html,body{width:1200px;height:2164px;overflow:hidden;background:var(--white);font-family:"Poppins",Arial,sans-serif;color:var(--ink)}
.board{position:relative;width:1200px;height:2164px;overflow:hidden;background:var(--white)}
.board__accent{position:absolute;left:0;top:0}
.board__label{position:absolute;top:22px;font-size:22px;font-weight:600;color:var(--ink);text-align:center}
.brand-lockup{position:absolute;left:256px;top:1776px;display:flex;align-items:center;gap:18px}
.brand-lockup__mark{width:40px;height:40px;background:var(--orange)}
.brand-lockup__name{font-size:84px;font-weight:700;color:var(--ink);letter-spacing:2px;line-height:1}

/* ---------- desktop page ---------- */
.page{position:absolute;top:72px;width:472px;height:1648px;background:var(--white);box-shadow:0 0 10px rgba(0,0,0,.18);overflow:hidden;font-size:5px;line-height:1.5}
.page--v1{left:40px}
.page--v2{left:544px}
.nav{height:24px;display:flex;align-items:center;justify-content:space-between;padding:0 22px;background:var(--white)}
.logo{font-weight:700;color:var(--ink);font-size:10px;display:flex;align-items:center;gap:3px}
.logo__dot{width:5px;height:5px;background:var(--orange)}
.nav__links{display:flex;gap:10px;color:var(--ink);font-weight:500;align-items:center}
.btn{display:inline-block;background:var(--orange);color:var(--white);border-radius:20px;padding:2px 9px;font-weight:600;font-size:5px}
.hero{position:relative;height:192px;overflow:hidden}
.photo{background:linear-gradient(135deg,#8b8f96,#4a4f58 55%,#2c3038)}
.photo--warm{background:linear-gradient(135deg,#d9d3cb,#a79c92 50%,#6c6660)}
.photo--office{background:linear-gradient(160deg,#c7ccd2,#8f98a3 60%,#5d6570)}
.hero__photo{position:absolute;inset:0}
.hero__overlay{position:absolute;left:0;top:0;bottom:0;width:62%;clip-path:polygon(0 0,100% 0,78% 100%,0 100%)}
.page--v1 .hero__overlay{background:linear-gradient(90deg,rgba(242,107,29,.95),rgba(242,107,29,.75))}
.page--v2 .hero__overlay{background:linear-gradient(90deg,rgba(30,35,45,.95),rgba(30,35,45,.7))}
.hero__text{position:absolute;left:24px;top:56px;color:var(--white)}
.hero__title{font-size:17px;font-weight:700;line-height:1.15;margin-bottom:10px}
.page--v1 .hero .btn{background:var(--dark)}
.welcome{height:184px;display:flex;align-items:center;padding:0 34px;gap:30px}
.welcome__heading{flex:0 0 120px}
.welcome__small{font-size:11px;font-weight:600}
.welcome__small span{color:var(--orange)}
.welcome__big{font-size:22px;font-weight:700;line-height:1}
.welcome__body{flex:1;color:var(--grey)}
.welcome__body p{margin-bottom:8px}
.section-title{text-align:center;font-size:13px;font-weight:700;color:var(--orange)}
.section-title span{color:var(--ink)}
.dark .section-title span{color:var(--white)}
.section-title::after{content:"";display:block;width:16px;height:1.5px;background:var(--orange);margin:3px auto 0}
.dark{background:var(--dark);color:var(--white)}
.products{position:relative;height:288px;padding-top:34px}
.products__edge{position:absolute;left:0;width:100%;height:14px;background:var(--orange)}
.products__edge--top{top:0;clip-path:polygon(0 0,100% 0,100% 20%,60% 100%,40% 100%,0 20%)}
.products__edge--bottom{bottom:0;clip-path:polygon(0 80%,40% 0,60% 0,100% 80%,100% 100%,0 100%)}
.products__row{display:flex;justify-content:center;gap:22px;margin-top:14px}
.product-card{width:100px;height:190px;background:var(--white);border-radius:50px;border:3px solid var(--orange);color:var(--ink);text-align:center;padding:14px 10px;display:flex;flex-direction:column;align-items:center;gap:6px}
.product-card__icon{width:50px;height:50px;border-radius:50%;background:var(--orange);border:4px solid var(--orange-soft)}
.product-card__title{font-weight:700;font-size:6px;color:var(--orange)}
.product-card__text{color:var(--grey)}
.services{height:180px;padding-top:18px}
.cards{display:flex;justify-content:center;gap:14px;margin-top:12px}
.card{width:118px}
.card__img{height:62px}
.card__title{font-weight:600;font-size:6px;margin-top:5px}
.card__text{color:var(--grey)}
.team{height:220px;padding-top:22px}
.team__row{display:flex;justify-content:center;gap:24px;margin-top:20px}
.member{text-align:center;width:64px}
.member__photo{width:62px;height:62px;border-radius:50%;border:3px solid var(--orange)}
.member__name{font-weight:600;font-size:6px;margin-top:6px}
.member__role{color:#b6bac2}
.news{height:220px;padding-top:22px}
.news .card__img{height:70px}
.contact{height:200px;padding-top:24px;background:linear-gradient(180deg,var(--dark),var(--dark-2))}
.form{width:300px;margin:16px auto 0;display:flex;flex-direction:column;gap:6px}
.form__row{display:flex;gap:6px}
.field{flex:1;height:16px;background:var(--dark-2);border:1px solid #4a505c;color:#9aa0aa;padding:3px 6px}
.field--area{height:48px}
.form .btn{align-self:center;margin-top:4px}
.footer{height:140px;display:flex;padding:26px 30px;gap:28px}
.footer__brand{flex:0 0 120px;color:var(--grey)}
.footer__brand .logo{margin-bottom:8px}
.footer__col{flex:1;color:var(--grey)}
.footer__col h4{color:var(--ink);font-size:6px;margin-bottom:4px}
.socials{display:flex;gap:4px;margin-top:10px}
.socials i{width:10px;height:10px;border-radius:50%;background:var(--orange);display:block}

/* ---------- mobile page ---------- */
.mobile{position:absolute;left:1048px;top:72px;width:112px;height:2048px;background:var(--white);box-shadow:0 0 10px rgba(0,0,0,.25);overflow:hidden;font-size:3.5px;line-height:1.5}
.mobile .nav{height:16px;padding:0 7px}
.mobile .logo{font-size:6px}
.m-burger{width:8px;height:5px;border-top:1px solid var(--ink);border-bottom:1px solid var(--ink)}
.mobile .btn{font-size:3.5px;padding:1px 5px}
.m-hero{position:relative;height:92px}
.m-hero .hero__overlay{width:85%;background:rgba(242,107,29,.9)}
.m-hero__text{position:absolute;left:7px;top:26px;color:var(--white)}
.m-hero__text .hero__title{font-size:8px;margin-bottom:5px}
.m-welcome{height:140px;padding:18px 8px;color:var(--grey)}
.m-welcome .welcome__small{font-size:6px;color:var(--ink)}
.m-welcome .welcome__big{font-size:11px;color:var(--ink);margin-bottom:8px}
.m-welcome p{margin-bottom:6px}
.mobile .section-title{font-size:7px}
.m-products{height:580px;padding-top:18px;position:relative}
.m-products .product-card{width:76px;height:160px;margin:14px auto 0;border-radius:38px;padding:10px 6px;font-size:3.5px}
.m-products .product-card__icon{width:36px;height:36px}
.m-products .product-card__title{font-size:4.5px}
.m-services{height:300px;padding-top:16px}
.m-card{width:88px;margin:10px auto 0}
.m-card .card__img{height:50px}
.m-card .card__title{font-size:4.5px}
.m-team{height:260px;padding-top:16px}
.m-team__grid{display:grid;grid-template-columns:1fr 1fr;gap:10px 6px;padding:14px 10px 0}
.m-team .member{width:auto}
.m-team .member__photo{width:40px;height:40px;margin:0 auto}
.m-team .member__name{font-size:4px}
.m-news{height:220px;padding-top:16px}
.m-news .card__img{height:56px}
.m-contact{height:180px;padding-top:16px;background:linear-gradient(180deg,var(--dark),var(--dark-2))}
.m-contact .form{width:92px;margin-top:10px;gap:4px}
.m-contact .form__row{flex-direction:column;gap:4px}
.m-contact .field{height:11px;padding:2px 4px}
.m-contact .field--area{height:34px}
.m-footer{height:260px;padding:18px 10px;color:var(--grey)}
.m-footer .logo{margin-bottom:6px}
.m-footer h4{color:var(--ink);font-size:4.5px;margin:10px 0 3px}
.m-footer .socials i{width:7px;height:7px}
</style>
</head>
<body>
<div class="board">
  <svg class="board__accent" width="1200" height="2164" viewBox="0 0 1200 2164" aria-hidden="true">
    <polygon points="600,2164 1200,1260 1200,2164" fill="var(--orange)"/>
    <polygon points="700,2164 1200,1410 1200,1450 728,2164" fill="#ffffff" opacity=".9"/>
  </svg>

  <div class="board__label" style="left:40px;width:472px">Home Page V. 01</div>
  <div class="board__label" style="left:544px;width:472px">Home Page V. 02</div>
  <div class="board__label" style="left:1040px;width:128px">Mobile View</div>

  <!-- Home page version one -->
  <div class="page page--v1">
    <header class="nav">
      <div class="logo"><span class="logo__dot"></span>velora</div>
      <nav class="nav__links"><span>Home</span><span>Products</span><span>Services</span><span>Team</span><span>News</span><span class="btn">Contact</span></nav>
    </header>
    <section class="hero">
      <div class="hero__photo photo" role="img" aria-label="Photo of a team working at laptops in an office"></div>
      <div class="hero__overlay"></div>
      <div class="hero__text"><h1 class="hero__title">We are Developing<br>Several Products</h1><span class="btn">Read More</span></div>
    </section>
    <section class="welcome">
      <div class="welcome__heading"><div class="welcome__small">Welcome <span>to</span></div><div class="welcome__big">velora</div></div>
      <div class="welcome__body"><p>We build standard software for many sectors and craft custom tools for teams of any size. Our apps run on laptops, desktops, phones and tablets, and our consulting helps you streamline daily processes.</p><span class="btn">Read More</span></div>
    </section>
    <section class="products dark">
      <div class="products__edge products__edge--top"></div>
      <h2 class="section-title">Our <span>Product</span></h2>
      <div class="products__row">
        <div class="product-card"><div class="product-card__icon"></div><div class="product-card__title">Healthcare Planner</div><div class="product-card__text">Shift planning for clinics and care teams.</div><span class="btn">Read More</span></div>
        <div class="product-card"><div class="product-card__icon"></div><div class="product-card__title">Club Booking</div><div class="product-card__text">Court and class booking for sport clubs.</div><span class="btn">Read More</span></div>
        <div class="product-card"><div class="product-card__icon"></div><div class="product-card__title">Competition Manager</div><div class="product-card__text">Scoring and events for shooting sports.</div><span class="btn">Read More</span></div>
      </div>
      <div class="products__edge products__edge--bottom"></div>
    </section>
    <section class="services">
      <h2 class="section-title">Our <span>Services</span></h2>
      <div class="cards">
        <div class="card"><div class="card__img photo--office" role="img" aria-label="Photo of a desk with a laptop"></div><div class="card__title">Custom Software</div><div class="card__text">Tailored apps built around your workflow.</div></div>
        <div class="card"><div class="card__img photo--warm" role="img" aria-label="Photo of a consulting meeting"></div><div class="card__title">Consulting</div><div class="card__text">We help optimize your business processes.</div></div>
        <div class="card"><div class="card__img photo" role="img" aria-label="Photo of a developer at work"></div><div class="card__title">Support</div><div class="card__text">Reliable help for every product we ship.</div></div>
      </div>
    </section>
    <section class="team dark">
      <h2 class="section-title">Our <span>Team Member</span></h2>
      <div class="team__row">
        <div class="member"><div class="member__photo photo--warm" role="img" aria-label="Portrait of a founder"></div><div class="member__name">Jonas Weber</div><div class="member__role">Founder</div></div>
        <div class="member"><div class="member__photo photo--office" role="img" aria-label="Portrait of a founder"></div><div class="member__name">Lena Brandt</div><div class="member__role">Founder</div></div>
        <div class="member"><div class="member__photo photo--warm" role="img" aria-label="Portrait of a developer"></div><div class="member__name">Tim Keller</div><div class="member__role">Developer</div></div>
        <div class="member"><div class="member__photo photo--office" role="img" aria-label="Portrait of a designer"></div><div class="member__name">Mara Vogt</div><div class="member__role">Designer</div></div>
      </div>
    </section>
    <section class="news">
      <h2 class="section-title">Latest <span>News</span></h2>
      <div class="cards">
        <div class="card"><div class="card__img photo--office" role="img" aria-label="Photo of a laptop on a desk"></div><div class="card__title">New planner release</div><div class="card__text">Fresh features for care teams this month.</div></div>
        <div class="card"><div class="card__img photo--warm" role="img" aria-label="Photo of a phone in hand"></div><div class="card__title">Mobile app update</div><div class="card__text">Booking now faster on every device.</div></div>
        <div class="card"><div class="card__img photo" role="img" aria-label="Photo of a team meeting"></div><div class="card__title">Team grows</div><div class="card__text">Two new colleagues joined our crew.</div></div>
      </div>
    </section>
    <section class="contact dark">
      <h2 class="section-title">Get <span>In Touch</span></h2>
      <div class="form">
        <div class="form__row"><div class="field">Name</div><div class="field">Email</div></div>
        <div class="form__row"><div class="field">Phone</div><div class="field">Subject</div></div>
        <div class="field field--area">Message</div>
        <span class="btn">Send Message</span>
      </div>
    </section>
    <footer class="footer">
      <div class="footer__brand"><div class="logo"><span class="logo__dot"></span>velora</div>Software for many sectors, built by a young team.<div class="socials"><i></i><i></i><i></i><i></i></div></div>
      <div class="footer__col"><h4>Links</h4>Home<br>Products<br>Services<br>Team</div>
      <div class="footer__col"><h4>Products</h4>Planner<br>Booking<br>Competition</div>
      <div class="footer__col"><h4>Contact</h4>12 Sample Street<br>info@velora.example<br>+00 123 456 789</div>
    </footer>
  </div>

  <!-- Home page version two -->
  <div class="page page--v2">
    <header class="nav">
      <div class="logo"><span class="logo__dot"></span>velora</div>
      <nav class="nav__links"><span>Home</span><span>Products</span><span>Services</span><span>Team</span><span>News</span><span class="btn">Contact</span></nav>
    </header>
    <section class="hero">
      <div class="hero__photo photo" role="img" aria-label="Photo of a team working at laptops in an office"></div>
      <div class="hero__overlay"></div>
      <div class="hero__text"><h1 class="hero__title">We are Developing<br>Several Products</h1><span class="btn">Read More</span></div>
    </section>
    <section class="welcome">
      <div class="welcome__heading"><div class="welcome__small">Welcome <span>to</span></div><div class="welcome__big">velora</div></div>
      <div class="welcome__body"><p>We build standard software for many sectors and craft custom tools for teams of any size. Our apps run on laptops, desktops, phones and tablets, and our consulting helps you streamline daily processes.</p><span class="btn">Read More</span></div>
    </section>
    <section class="products dark">
      <div class="products__edge products__edge--top"></div>
      <h2 class="section-title">Our <span>Product</span></h2>
      <div class="products__row">
        <div class="product-card"><div class="product-card__icon"></div><div class="product-card__title">Healthcare Planner</div><div class="product-card__text">Shift planning for clinics and care teams.</div><span class="btn">Read More</span></div>
        <div class="product-card"><div class="product-card__icon"></div><div class="product-card__title">Club Booking</div><div class="product-card__text">Court and class booking for sport clubs.</div><span class="btn">Read More</span></div>
        <div class="product-card"><div class="product-card__icon"></div><div class="product-card__title">Competition Manager</div><div class="product-card__text">Scoring and events for shooting sports.</div><span class="btn">Read More</span></div>
      </div>
      <div class="products__edge products__edge--bottom"></div>
    </section>
    <section class="services">
      <h2 class="section-title">Our <span>Services</span></h2>
      <div class="cards">
        <div class="card"><div class="card__img photo--office" role="img" aria-label="Photo of a desk with a laptop"></div><div class="card__title">Custom Software</div><div class="card__text">Tailored apps built around your workflow.</div></div>
        <div class="card"><div class="card__img photo--warm" role="img" aria-label="Photo of a consulting meeting"></div><div class="card__title">Consulting</div><div class="card__text">We help optimize your business processes.</div></div>
        <div class="card"><div class="card__img photo" role="img" aria-label="Photo of a developer at work"></div><div class="card__title">Support</div><div class="card__text">Reliable help for every product we ship.</div></div>
      </div>
    </section>
    <section class="team dark">
      <h2 class="section-title">Our <span>Team Member</span></h2>
      <div class="team__row">
        <div class="member"><div class="member__photo photo--warm" role="img" aria-label="Portrait of a founder"></div><div class="member__name">Jonas Weber</div><div class="member__role">Founder</div></div>
        <div class="member"><div class="member__photo photo--office" role="img" aria-label="Portrait of a founder"></div><div class="member__name">Lena Brandt</div><div class="member__role">Founder</div></div>
        <div class="member"><div class="member__photo photo--warm" role="img" aria-label="Portrait of a developer"></div><div class="member__name">Tim Keller</div><div class="member__role">Developer</div></div>
        <div class="member"><div class="member__photo photo--office" role="img" aria-label="Portrait of a designer"></div><div class="member__name">Mara Vogt</div><div class="member__role">Designer</div></div>
      </div>
    </section>
    <section class="news">
      <h2 class="section-title">Latest <span>News</span></h2>
      <div class="cards">
        <div class="card"><div class="card__img photo--office" role="img" aria-label="Photo of a laptop on a desk"></div><div class="card__title">New planner release</div><div class="card__text">Fresh features for care teams this month.</div></div>
        <div class="card"><div class="card__img photo--warm" role="img" aria-label="Photo of a phone in hand"></div><div class="card__title">Mobile app update</div><div class="card__text">Booking now faster on every device.</div></div>
        <div class="card"><div class="card__img photo" role="img" aria-label="Photo of a team meeting"></div><div class="card__title">Team grows</div><div class="card__text">Two new colleagues joined our crew.</div></div>
      </div>
    </section>
    <section class="contact dark">
      <h2 class="section-title">Get <span>In Touch</span></h2>
      <div class="form">
        <div class="form__row"><div class="field">Name</div><div class="field">Email</div></div>
        <div class="form__row"><div class="field">Phone</div><div class="field">Subject</div></div>
        <div class="field field--area">Message</div>
        <span class="btn">Send Message</span>
      </div>
    </section>
    <footer class="footer">
      <div class="footer__brand"><div class="logo"><span class="logo__dot"></span>velora</div>Software for many sectors, built by a young team.<div class="socials"><i></i><i></i><i></i><i></i></div></div>
      <div class="footer__col"><h4>Links</h4>Home<br>Products<br>Services<br>Team</div>
      <div class="footer__col"><h4>Products</h4>Planner<br>Booking<br>Competition</div>
      <div class="footer__col"><h4>Contact</h4>12 Sample Street<br>info@velora.example<br>+00 123 456 789</div>
    </footer>
  </div>

  <!-- Mobile view -->
  <div class="mobile">
    <header class="nav"><div class="logo"><span class="logo__dot"></span>velora</div><div class="m-burger"></div></header>
    <section class="m-hero">
      <div class="hero__photo photo" role="img" aria-label="Photo of a team working at laptops in an office"></div>
      <div class="hero__overlay"></div>
      <div class="m-hero__text"><h1 class="hero__title">We are Developing<br>Several Products</h1><span class="btn">Read More</span></div>
    </section>
    <section class="m-welcome">
      <div class="welcome__small">Welcome <span style="color:var(--orange)">to</span></div>
      <div class="welcome__big">velora</div>
      <p>We build standard software for many sectors and custom tools for teams of any size, on every device.</p>
      <span class="btn">Read More</span>
    </section>
    <section class="m-products dark">
      <h2 class="section-title">Our <span>Product</span></h2>
      <div class="product-card"><div class="product-card__icon"></div><div class="product-card__title">Healthcare Planner</div><div class="product-card__text">Shift planning for care teams.</div><span class="btn">Read More</span></div>
      <div class="product-card"><div class="product-card__icon"></div><div class="product-card__title">Club Booking</div><div class="product-card__text">Booking for sport clubs.</div><span class="btn">Read More</span></div>
      <div class="product-card"><div class="product-card__icon"></div><div class="product-card__title">Competition Manager</div><div class="product-card__text">Scoring for shooting sports.</div><span class="btn">Read More</span></div>
    </section>
    <section class="m-services">
      <h2 class="section-title">Our <span>Services</span></h2>
      <div class="m-card"><div class="card__img photo--office" role="img" aria-label="Photo of a desk with a laptop"></div><div class="card__title">Custom Software</div><div class="card__text">Tailored apps for your workflow.</div></div>
      <div class="m-card"><div class="card__img photo--warm" role="img" aria-label="Photo of a consulting meeting"></div><div class="card__title">Consulting</div><div class="card__text">Optimize your processes.</div></div>
      <div class="m-card"><div class="card__img photo" role="img" aria-label="Photo of a developer at work"></div><div class="card__title">Support</div><div class="card__text">Help for every product.</div></div>
    </section>
    <section class="m-team dark">
      <h2 class="section-title">Our <span>Team Member</span></h2>
      <div class="m-team__grid">
        <div class="member"><div class="member__photo photo--warm" role="img" aria-label="Portrait of a founder"></div><div class="member__name">Jonas Weber</div><div class="member__role">Founder</div></div>
        <div class="member"><div class="member__photo photo--office" role="img" aria-label="Portrait of a founder"></div><div class="member__name">Lena Brandt</div><div class="member__role">Founder</div></div>
        <div class="member"><div class="member__photo photo--warm" role="img" aria-label="Portrait of a developer"></div><div class="member__name">Tim Keller</div><div class="member__role">Developer</div></div>
        <div class="member"><div class="member__photo photo--office" role="img" aria-label="Portrait of a designer"></div><div class="member__name">Mara Vogt</div><div class="member__role">Designer</div></div>
      </div>
    </section>
    <section class="m-news">
      <h2 class="section-title">Latest <span>News</span></h2>
      <div class="m-card"><div class="card__img photo--office" role="img" aria-label="Photo of a laptop on a desk"></div><div class="card__title">New planner release</div><div class="card__text">Fresh features for care teams.</div></div>
      <div class="m-card"><div class="card__img photo--warm" role="img" aria-label="Photo of a phone in hand"></div><div class="card__title">Mobile app update</div><div class="card__text">Booking now faster.</div></div>
    </section>
    <section class="m-contact dark">
      <h2 class="section-title">Get <span>In Touch</span></h2>
      <div class="form">
        <div class="form__row"><div class="field">Name</div><div class="field">Email</div><div class="field">Phone</div></div>
        <div class="field field--area">Message</div>
        <span class="btn">Send</span>
      </div>
    </section>
    <footer class="m-footer">
      <div class="logo"><span class="logo__dot"></span>velora</div>
      Software for many sectors, built by a young team.
      <h4>Links</h4>Home<br>Products<br>Services<br>Team
      <h4>Products</h4>Planner<br>Booking<br>Competition
      <h4>Contact</h4>12 Sample Street<br>info@velora.example<br>+00 123 456 789
      <div class="socials"><i></i><i></i><i></i><i></i></div>
    </footer>
  </div>

  <div class="brand-lockup"><span class="brand-lockup__mark"></span><span class="brand-lockup__name">velora</span></div>
</div>
</body>
</html>
```